Sleek & Sexy MedSpa Direct Mailer Needed for High End Client

We need an eye catching and elegant direct mailer for our client Orla Renn Medical Spa. Please stay with black & white tones. They like Tessa Vornhalt brand looks - sleek & sexy & high end.

Here is the template layout: https://printcrate.com/offering/coupon-mailer you can download a PDF or IDML on that page.

Website: https://orlarennmedicalspa.com/
Logo: https://files.stowbin.net/folders/7qkTe3Hw9pLzXc2-Vbn8RmYd4Jf_Ga6s?usp=sharing

Offers:
New Year/ New You! Make your beauty dreams a reality!
15% off laser hair removal packages
$50 off Lumirex or Faciquin
$75 off 1 Filler syringe
15% off QM products

Call today to learn more & make sure to mention MAIL OFFER!

```html
<!DOCTYPE html>
<html lang="en">
<head>
<meta charset="utf-8">
<title>Orla Renn Medical Spa — Coupon Mailer</title>
<link href="https://fonts.googleapis.com/css2?family=Montserrat:wght@300;400;500;600&display=swap" rel="stylesheet">
<style>
  :root{
    --page:#ffffff;
    --ink:#1c1c1c;
    --ink-soft:#4a4a4a;
    --muted:#8c8c8c;
    --paper:#f1f1f1;
    --coupon-fill:#ececec;
    --coupon-edge:#9c9c9c;
    --line:#7a7a7a;
  }
  *{box-sizing:border-box;margin:0;padding:0}
  html,body{width:673px;height:1200px;overflow:hidden;background:var(--page)}
  body{font-family:"Montserrat",sans-serif;color:var(--ink);position:relative}

  .spread{position:absolute;left:26px;width:620px;height:301px;overflow:hidden;
    background:linear-gradient(180deg,#f4f4f4 0%,#ececec 55%,#e2e2e2 100%);
    box-shadow:0 6px 14px rgba(0,0,0,.18)}
  .spread--inside{top:279px}
  .spread--outside{top:620px}

  .backdrop{position:absolute;inset:0;
    background:
      radial-gradient(ellipse 60% 90% at 70% 0%,rgba(255,255,255,.9) 0%,rgba(255,255,255,0) 70%),
      radial-gradient(ellipse 40% 80% at 45% 10%,rgba(205,205,205,.45) 0%,rgba(205,205,205,0) 70%),
      linear-gradient(180deg,rgba(255,255,255,0) 50%,rgba(180,180,180,.35) 100%)}

  .black-band{position:absolute;top:0;left:0;height:100%;
    background:repeating-linear-gradient(90deg,#121212 0 2px,#1a1a1a 2px 4px)}

  /* coupons */
  .coupon{position:absolute;width:180px;height:78px}
  .coupon svg{position:absolute;inset:0}
  .coupon__tab{position:absolute;left:8px;top:6px;width:26px;height:66px;display:flex;align-items:center;justify-content:center}
  .coupon__tab-inner{transform:rotate(-90deg);white-space:nowrap;text-align:center;line-height:1}
  .coupon__num{font-size:8.5px;font-weight:300;color:var(--muted);letter-spacing:.3px;display:block}
  .coupon__valid{font-size:2.8px;color:var(--ink-soft);display:block;margin-top:1px;letter-spacing:.2px}
  .coupon__divider{position:absolute;left:38px;top:8px;height:62px;border-left:.8px dashed var(--muted)}
  .coupon__body{position:absolute;left:42px;right:8px;top:10px;text-align:center}
  .coupon__value{font-size:14px;font-weight:500;letter-spacing:-.2px;color:var(--ink)}
  .coupon__label{display:inline-block;margin-top:1px;padding:1px 7px;border:.7px solid var(--ink-soft);
    font-size:5px;letter-spacing:.6px;color:var(--ink-soft)}
  .coupon__fine{margin:4px auto 0;width:100px;font-size:3.2px;line-height:1.35;color:var(--ink-soft)}

  /* photo placeholders */
  .photo{position:absolute}
  .photo--staff{background:linear-gradient(180deg,#dcdcdc 0%,#a8a8a8 35%,#3c3c3c 60%,#2a2a2a 85%,#6a6a6a 100%)}
  .photo--hero{background:
      linear-gradient(90deg,rgba(0,0,0,0) 30%,rgba(40,40,40,.55) 42%,rgba(30,30,30,.65) 58%,rgba(0,0,0,0) 70%),
      linear-gradient(180deg,#f6f6f6 0%,#ececec 70%,#9a9a9a 84%,#6e6e6e 100%)}
  .photo--seated{background:
      radial-gradient(ellipse 40% 45% at 50% 30%,#bdbdbd 0%,rgba(189,189,189,0) 100%),
      radial-gradient(ellipse 60% 40% at 50% 80%,#cfcfcf 0%,rgba(207,207,207,0) 100%)}
  .photo--sea{background:linear-gradient(180deg,rgba(255,255,255,0) 0%,#dedede 30%,#c9c9c9 60%,#d6d6d6 100%)}

  .frame-window{position:absolute;left:214px;top:24px;width:161px;height:266px;border-radius:10px;
    background:linear-gradient(180deg,rgba(255,255,255,.95),rgba(248,248,248,.8))}
  .accent-lines{position:absolute;inset:0}

  .brand{position:absolute;text-align:center;font-weight:300;color:var(--ink);letter-spacing:.5px;line-height:1}
  .brand__name{display:block;font-size:15px}
  .brand__sub{display:block;font-size:5px;letter-spacing:2.4px;margin-top:2px}

  .headline{position:absolute;left:422px;top:206px;line-height:1.05}
  .headline__lead{font-size:12.5px;font-weight:300;color:var(--ink-soft)}
  .headline__main{font-size:14.5px;font-weight:400;letter-spacing:.2px}
  .headline__tail{font-size:12.5px;font-weight:300;color:var(--ink-soft)}
  .site-url{position:absolute;left:490px;top:271px;font-size:5px;font-weight:600;color:var(--ink)}

  .contact{position:absolute;left:258px;top:58px;width:126px;text-align:center;line-height:1.1}
  .contact__call{font-size:7.5px;font-weight:300;color:var(--ink-soft);letter-spacing:.4px}
  .contact__phone{font-size:9px;font-weight:600}
  .contact__social{display:flex;justify-content:center;gap:5px;margin:4px 0 3px}
  .contact__social span{width:5px;height:5px;border-radius:50%;background:var(--ink-soft)}
  .contact__address{font-size:4.6px;color:var(--ink-soft)}

  .offer{position:absolute;left:248px;top:119px;display:flex;gap:8px;align-items:flex-start}
  .offer__price{text-align:center;line-height:1}
  .offer__amount{font-size:17px;font-weight:500}
  .offer__amount sup{font-size:9px;font-weight:400}
  .offer__off{font-size:12px;font-weight:300;letter-spacing:.5px;margin-top:1px}
  .offer__service{line-height:1;font-size:11px;font-weight:400;letter-spacing:.2px}
  .offer__service .boxed{display:inline-block;border:.8px solid var(--ink);border-radius:2px;padding:0 2px}
  .offer__service .row{padding-left:2px}
  .offer__service .light{font-weight:300}

  .cta-vertical{position:absolute;left:158px;top:262px;transform-origin:left top;transform:rotate(-90deg);
    white-space:nowrap;color:var(--ink);line-height:1.05}
  .cta-vertical__title{font-size:7px;font-weight:500}
  .cta-vertical__text{font-size:6px;font-weight:300;color:var(--ink-soft)}
  .cta-vertical__text b{font-weight:600;color:var(--ink)}
</style>
</head>
<body>

<!-- Inside spread -->
<section class="spread spread--inside">
  <div class="backdrop"></div>
  <div class="photo photo--sea" role="img" aria-label="Soft seascape with shoreline and rocks" style="left:142px;top:120px;width:478px;height:181px"></div>
  <div class="black-band" style="width:142px"></div>

  <div class="frame-window"></div>
  <svg class="accent-lines" viewBox="0 0 620 301" aria-hidden="true">
    <g stroke="var(--line)" stroke-width=".8">
      <line x1="198" y1="48" x2="265" y2="10"/>
      <line x1="323" y1="10" x2="392" y2="48"/>
      <line x1="198" y1="255" x2="265" y2="292"/>
      <line x1="323" y1="292" x2="392" y2="255"/>
    </g>
  </svg>

  <div class="coupon" style="left:6px;top:30px">
    <svg viewBox="0 0 180 78"><path d="M6,1.5H174a4.5,4.5 0 0 1 4.5,4.5V30a9,9 0 0 0 0,18V72a4.5,4.5 0 0 1 -4.5,4.5H6a4.5,4.5 0 0 1 -4.5,-4.5V48a9,9 0 0 0 0,-18V6a4.5,4.5 0 0 1 4.5,-4.5Z" fill="var(--coupon-fill)" stroke="var(--coupon-edge)" stroke-width="3"/></svg>
    <div class="coupon__tab"><div class="coupon__tab-inner"><span class="coupon__num">COUPON 01</span><span class="coupon__valid">VALID UNTIL: 31 | 12 | 2023</span></div></div>
    <div class="coupon__divider"></div>
    <div class="coupon__body"><div class="coupon__value">$50 OFF</div><div class="coupon__label">LUMIREX OR FACIQUIN</div>
      <p class="coupon__fine">Present this coupon at your visit. One per client; not valid with other offers or promotions.</p></div>
  </div>
  <div class="coupon" style="left:6px;top:112px">
    <svg viewBox="0 0 180 78"><path d="M6,1.5H174a4.5,4.5 0 0 1 4.5,4.5V30a9,9 0 0 0 0,18V72a4.5,4.5 0 0 1 -4.5,4.5H6a4.5,4.5 0 0 1 -4.5,-4.5V48a9,9 0 0 0 0,-18V6a4.5,4.5 0 0 1 4.5,-4.5Z" fill="var(--coupon-fill)" stroke="var(--coupon-edge)" stroke-width="3"/></svg>
    <div class="coupon__tab"><div class="coupon__tab-inner"><span class="coupon__num">COUPON 02</span><span class="coupon__valid">VALID UNTIL: 31 | 12 | 2023</span></div></div>
    <div class="coupon__divider"></div>
    <div class="coupon__body"><div class="coupon__value">$75 OFF</div><div class="coupon__label">1 FILLER SYRINGE</div>
      <p class="coupon__fine">Present this coupon at your visit. One per client; not valid with other offers or promotions.</p></div>
  </div>
  <div class="coupon" style="left:6px;top:195px">
    <svg viewBox="0 0 180 78"><path d="M6,1.5H174a4.5,4.5 0 0 1 4.5,4.5V30a9,9 0 0 0 0,18V72a4.5,4.5 0 0 1 -4.5,4.5H6a4.5,4.5 0 0 1 -4.5,-4.5V48a9,9 0 0 0 0,-18V6a4.5,4.5 0 0 1 4.5,-4.5Z" fill="var(--coupon-fill)" stroke="var(--coupon-edge)" stroke-width="3"/></svg>
    <div class="coupon__tab"><div class="coupon__tab-inner"><span class="coupon__num">COUPON 03</span><span class="coupon__valid">VALID UNTIL: 31 | 12 | 2023</span></div></div>
    <div class="coupon__divider"></div>
    <div class="coupon__body"><div class="coupon__value">15% OFF</div><div class="coupon__label">QM PRODUCTS</div>
      <p class="coupon__fine">Present this coupon at your visit. One per client; not valid with other offers or promotions.</p></div>
  </div>

  <div class="brand" style="left:450px;top:37px;width:120px"><span class="brand__name">Orla Renn</span><span class="brand__sub">MEDICAL SPA</span></div>

  <div class="photo photo--staff" role="img" aria-label="Portrait of staff member one in dark blouse" style="left:420px;top:77px;width:56px;height:117px"></div>
  <div class="photo photo--staff" role="img" aria-label="Portrait of staff member two in polka dot blouse" style="left:481px;top:77px;width:56px;height:117px"></div>
  <div class="photo photo--staff" role="img" aria-label="Portrait of staff member three in black blazer" style="left:542px;top:77px;width:56px;height:117px"></div>

  <div class="headline">
    <div class="headline__lead">New Year | New You</div>
    <div class="headline__main">MAKE YOUR BEAUTY</div>
    <div class="headline__tail">dreams a reality</div>
  </div>
  <div class="site-url">www.orlarennmedicalspa.com</div>
</section>

<!-- Outside spread -->
<section class="spread spread--outside">
  <div class="backdrop"></div>
  <div class="black-band" style="width:182px"></div>
  <div class="photo photo--hero" role="img" aria-label="Spa specialist in black dress leaning against a white wall" style="left:27px;top:20px;width:123px;height:257px"></div>
  <svg class="accent-lines" viewBox="0 0 620 301" aria-hidden="true">
    <g stroke="#eeeeee" stroke-width=".9">
      <line x1="8" y1="48" x2="64" y2="10"/>
      <line x1="118" y1="292" x2="172" y2="258"/>
    </g>
  </svg>
  <div class="cta-vertical" style="left:122px;top:255px">
    <div class="cta-vertical__title">CALL TODAY</div>
    <div class="cta-vertical__text">to learn more &amp; make sure to mention <b>MAIL OFFER!</b></div>
  </div>

  <div class="photo photo--seated" role="img" aria-label="Smiling woman seated with knees drawn up" style="left:225px;top:160px;width:160px;height:141px"></div>

  <div class="brand" style="left:225px;top:26px;width:120px"><span class="brand__name">Orla Renn</span><span class="brand__sub">MEDICAL SPA</span></div>
  <div class="contact" style="left:222px">
    <div class="contact__call">CALL TODAY</div>
    <div class="contact__phone">401-555-0148</div>
    <div class="contact__social"><span></span><span></span><span></span><span></span></div>
    <div class="contact__address">2140 Harbor Lane<br>Westfield Cove, RI 02900</div>
  </div>

  <div class="offer" style="left:212px;top:117px">
    <div class="offer__price"><div class="offer__amount">15<sup>%</sup></div><div class="offer__off">-OFF-</div></div>
    <div class="offer__service"><span class="boxed">LASER HAIR</span><br><span class="row">REMOVAL</span><br><span class="row light">PACKAGES</span></div>
  </div>

  <div class="coupon" style="left:433px;top:28px">
    <svg viewBox="0 0 180 78"><path d="M6,1.5H174a4.5,4.5 0 0 1 4.5,4.5V30a9,9 0 0 0 0,18V72a4.5,4.5 0 0 1 -4.5,4.5H6a4.5,4.5 0 0 1 -4.5,-4.5V48a9,9 0 0 0 0,-18V6a4.5,4.5 0 0 1 4.5,-4.5Z" fill="var(--coupon-fill)" stroke="var(--coupon-edge)" stroke-width="3"/></svg>
    <div class="coupon__tab"><div class="coupon__tab-inner"><span class="coupon__num">COUPON 01</span><span class="coupon__valid">VALID UNTIL: 31 | 12 | 2023</span></div></div>
    <div class="coupon__divider"></div>
    <div class="coupon__body"><div class="coupon__value">$50 OFF</div><div class="coupon__label">LUMIREX OR FACIQUIN</div>
      <p class="coupon__fine">Present this coupon at your visit. One per client; not valid with other offers or promotions.</p></div>
  </div>
  <div class="coupon" style="left:433px;top:111px">
    <svg viewBox="0 0 180 78"><path d="M6,1.5H174a4.5,4.5 0 0 1 4.5,4.5V30a9,9 0 0 0 0,18V72a4.5,4.5 0 0 1 -4.5,4.5H6a4.5,4.5 0 0 1 -4.5,-4.5V48a9,9 0 0 0 0,-18V6a4.5,4.5 0 0 1 4.5,-4.5Z" fill="var(--coupon-fill)" stroke="var(--coupon-edge)" stroke-width="3"/></svg>
    <div class="coupon__tab"><div class="coupon__tab-inner"><span class="coupon__num">COUPON 02</span><span class="coupon__valid">VALID UNTIL: 31 | 12 | 2023</span></div></div>
    <div class="coupon__divider"></div>
    <div class="coupon__body"><div class="coupon__value">$75 OFF</div><div class="coupon__label">1 FILLER SYRINGE</div>
      <p class="coupon__fine">Present this coupon at your visit. One per client; not valid with other offers or promotions.</p></div>
  </div>
  <div class="coupon" style="left:433px;top:194px">
    <svg viewBox="0 0 180 78"><path d="M6,1.5H174a4.5,4.5 0 0 1 4.5,4.5V30a9,9 0 0 0 0,18V72a4.5,4.5 0 0 1 -4.5,4.5H6a4.5,4.5 0 0 1 -4.5,-4.5V48a9,9 0 0 0 0,-18V6a4.5,4.5 0 0 1 4.5,-4.5Z" fill="var(--coupon-fill)" stroke="var(--coupon-edge)" stroke-width="3"/></svg>
    <div class="coupon__tab"><div class="coupon__tab-inner"><span class="coupon__num">COUPON 03</span><span class="coupon__valid">VALID UNTIL: 31 | 12 | 2023</span></div></div>
    <div class="coupon__divider"></div>
    <div class="coupon__body"><div class="coupon__value">15% OFF</div><div class="coupon__label">QM PRODUCTS</div>
      <p class="coupon__fine">Present this coupon at your visit. One per client; not valid with other offers or promotions.</p></div>
  </div>
</section>

</body>
</html>
```